Business Card Design & Gift cards, Gift Cert, Donation Card

Retail Gift Store-in addition to Business Cards we'd like sequenced 2 sided Gift cards, Gift Certificate Cards, and Donation Cards.please see examples and email for clarificationlogos attached with examples-
Gift Card, Gift Certificate and Donation Card will all be same style just differant upper right title, with back side info as example.
business card, as example is single sided.
looking for additional ideas for layout

Industry/Entity Type

Business

Contact Information for Business Card

211 Newman St.East Tawas, MI 48730989.362.8730Office@BrewKrew.com

Requirements
Must have
• Blue as per example
• Logos provided
• like gradiant background

```html
<!DOCTYPE html>
<html lang="en">
<head>
<meta charset="utf-8">
<title>Tillow Marsh – Business Card</title>
<link href="https://fonts.googleapis.com/css2?family=Open+Sans:wght@400;600&display=swap" rel="stylesheet">
<style>
  :root {
    --page-bg: #e9ecf1;
    --royal-blue: #4565c4;
    --royal-blue-dark: #3a55ad;
    --sky-top: #a9c8ea;
    --sky-bottom: #f2f6fb;
    --rule-grey: #a8aab0;
    --ink: #1d1f24;
    --brand-blue: #4a5fc0;
  }
  * { box-sizing: border-box; margin: 0; padding: 0; }
  html, body {
    width: 1200px; height: 892px; overflow: hidden;
    background: var(--page-bg);
    font-family: "Open Sans", Arial, sans-serif;
  }
  .sheet {
    width: 1200px; height: 892px;
    display: flex; align-items: center; justify-content: center; gap: 48px;
  }
  .card {
    position: relative;
    width: 540px; height: 309px;
    border-radius: 4px;
    overflow: hidden;
    box-shadow: 0 6px 18px rgba(20, 30, 60, 0.18);
  }
  .card-front {
    background: linear-gradient(160deg, var(--sky-bottom) 0%, #dfeaf6 45%, var(--sky-top) 100%);
  }
  .card-back {
    background: linear-gradient(200deg, var(--sky-top) 0%, #dde8f5 50%, var(--sky-bottom) 100%);
  }
  .card-shapes { position: absolute; inset: 0; width: 100%; height: 100%; }

  .brand-name {
    position: absolute;
    font-weight: 400;
    letter-spacing: 0.04em;
    color: var(--brand-blue);
    display: flex; align-items: center; gap: 10px;
    white-space: nowrap;
    line-height: 1;
  }
  .brand-dot {
    width: 14px; height: 14px; border-radius: 50%;
    background: var(--brand-blue);
  }
  .card-front .brand-name { left: 34px; bottom: 74px; font-size: 34px; }
  .card-back .brand-name {
    left: 50%; top: 50%; transform: translate(-50%, -50%);
    font-size: 44px; color: var(--ink);
  }
  .card-back .brand-dot { background: var(--ink); width: 16px; height: 16px; }

  .contact-list {
    position: absolute; right: 26px; top: 92px;
    list-style: none;
    display: flex; flex-direction: column; gap: 9px;
    font-size: 14.5px; line-height: 1.3; color: var(--ink);
  }
  .contact-item { display: flex; align-items: center; justify-content: flex-end; gap: 10px; }
  .contact-icon {
    width: 14px; height: 14px; flex: none;
    background: var(--royal-blue); border-radius: 2px;
    display: flex; align-items: center; justify-content: center;
  }
  .contact-icon svg { width: 10px; height: 10px; }
</style>
</head>
<body>
<main class="sheet">

  <section class="card card-front" aria-label="Business card front">
    <svg class="card-shapes" viewBox="0 0 540 309" preserveAspectRatio="none" aria-hidden="true">
      <path d="M0 0 H540 V72 C460 36 330 14 170 0 Z" fill="var(--royal-blue)"/>
      <path d="M170 0 C330 14 460 36 540 72" fill="none" stroke="var(--rule-grey)" stroke-width="4"/>
      <path d="M300 309 L340 255 H540 V309 Z" fill="var(--royal-blue-dark)"/>
    </svg>

    <ul class="contact-list">
      <li class="contact-item">989.517.4296
        <span class="contact-icon"><svg viewBox="0 0 10 10"><path d="M2 1 L4 1 L4.6 3 L3.5 3.8 C4 5 5 6 6.2 6.5 L7 5.4 L9 6 L9 8 C5 8.5 1.5 5 2 1 Z" fill="#fff"/></svg></span>
      </li>
      <li class="contact-item">Office@TillowMarsh.com
        <span class="contact-icon"><svg viewBox="0 0 10 10"><rect x="1" y="2.5" width="8" height="5" fill="none" stroke="#fff" stroke-width="1"/><path d="M1 2.5 L5 5.5 L9 2.5" fill="none" stroke="#fff" stroke-width="1"/></svg></span>
      </li>
      <li class="contact-item">482 Larkfield Ave. Corvale Bay, MI 49301
        <span class="contact-icon"><svg viewBox="0 0 10 10"><path d="M5 9 C3 6.5 2 5 2 3.8 A3 3 0 0 1 8 3.8 C8 5 7 6.5 5 9 Z" fill="#fff"/><circle cx="5" cy="3.8" r="1.1" fill="var(--royal-blue)"/></svg></span>
      </li>
    </ul>

    <div class="brand-name"><span class="brand-dot"></span>TILLOW MARSH</div>
  </section>

  <section class="card card-back" aria-label="Business card back">
    <div class="brand-name"><span class="brand-dot"></span>TILLOW MARSH</div>
  </section>

</main>
</body>
</html>
```